Awesome business card design needed

We need a new business card design to go with our new logo.
We are a web development agency that specialises in highly complex back-end integrations as opposed to design, our customers are retailers, hotels, hospitals and any other organisation that has a large online marketing department.
Take a look at our website - www.brenoloft.com for some inspiration.
We want our new business cards to exude class, professionalism and style.
We are likely to choose a high-end card to print them on but we want the design of the card itself to really turn heads.
We have no specific colour requirements, the logo as you will see is a turquoise colour R89 G171 B167 #59aba7 but it can also be in white if you want to make the colour of the card something different.
The information on the card should be:
Name
Position
Tel
email
Potentially a double sided card could have our web address, twitter and FB links.

```html
<!DOCTYPE html>
<html lang="en">
<head>
<meta charset="utf-8">
<title>Brenoloft Business Card</title>
<link rel="stylesheet" href="https://fonts.googleapis.com/css2?family=Open+Sans:wght@400;600;700;800&display=swap">
<style>
  :root {
    --teal: #59aba7;
    --white: #ffffff;
    --swoosh: #3a3a3c;
    --stage: #e9e9e7;
    --card-shadow: rgba(0, 0, 0, 0.18);
  }
  * { box-sizing: border-box; margin: 0; padding: 0; }
  html, body {
    width: 1200px;
    height: 720px;
    overflow: hidden;
    background: var(--stage);
    font-family: "Open Sans", Arial, sans-serif;
  }
  .stage {
    position: relative;
    width: 1200px;
    height: 720px;
  }
  .card {
    position: absolute;
    top: 205px;
    width: 540px;
    height: 309px;
    overflow: hidden;
    box-shadow: 0 6px 18px var(--card-shadow);
  }
  .card--front { left: 40px; background: var(--white); }
  .card--back { left: 620px; background: var(--teal); }

  .card__shape { position: absolute; inset: 0; width: 100%; height: 100%; }

  .wordmark {
    position: absolute;
    font-weight: 800;
    letter-spacing: 1px;
    line-height: 1;
  }
  .card--front .wordmark {
    left: 70px;
    top: 42px;
    font-size: 74px;
    color: var(--teal);
  }
  .card--back .wordmark {
    left: 0;
    right: 0;
    top: 88px;
    text-align: center;
    font-size: 84px;
    color: var(--white);
  }

  .identity {
    position: absolute;
    right: 300px;
    top: 190px;
    text-align: right;
    color: var(--white);
    font-size: 12px;
    line-height: 1.35;
  }
  .identity__name { font-size: 15px; font-weight: 700; }
  .identity__role { margin-bottom: 6px; }

  .divider {
    position: absolute;
    left: 254px;
    top: 178px;
    width: 1px;
    height: 74px;
    background: var(--white);
  }

  .contacts {
    position: absolute;
    left: 268px;
    top: 172px;
    list-style: none;
    color: var(--white);
    font-size: 12px;
  }
  .contacts__item {
    display: flex;
    align-items: center;
    gap: 8px;
    height: 26px;
  }
  .contacts__icon { width: 12px; height: 12px; flex: none; }

  .follow {
    position: absolute;
    left: 0;
    right: 0;
    top: 212px;
    display: flex;
    justify-content: center;
    align-items: center;
    gap: 10px;
    color: var(--white);
    font-size: 16px;
    font-weight: 600;
  }
  .follow__badge {
    width: 26px;
    height: 26px;
    border-radius: 5px;
    background: var(--white);
  }
  .web-address {
    position: absolute;
    left: 0;
    right: 0;
    top: 252px;
    text-align: center;
    color: var(--white);
    font-size: 16px;
    font-weight: 600;
    letter-spacing: 1.5px;
  }
</style>
</head>
<body>
<main class="stage">

  <section class="card card--front" aria-label="Business card front">
    <svg class="card__shape" viewBox="0 0 540 309" preserveAspectRatio="none" aria-hidden="true">
      <path d="M0 309 L0 262 C 110 168, 330 120, 540 114 L540 309 Z" fill="var(--teal)"/>
      <path d="M0 256 C 110 156, 330 110, 540 104 L540 110 C 330 118, 110 164, 0 266 Z" fill="var(--swoosh)"/>
    </svg>

    <div class="wordmark">brenoloft</div>

    <div class="identity">
      <p class="identity__name">Your Name</p>
      <p class="identity__role">Position</p>
      <p>Street Name, City Name</p>
      <p>State Zip Code</p>
    </div>

    <span class="divider" aria-hidden="true"></span>

    <ul class="contacts">
      <li class="contacts__item">
        <svg class="contacts__icon" viewBox="0 0 12 12" aria-hidden="true">
          <circle cx="6" cy="6" r="5.3" fill="none" stroke="#fff" stroke-width="1.2"/>
          <path d="M4 3.2 L5 3 L5.6 4.6 L5 5.1 C5.3 5.9 6 6.7 6.9 7 L7.4 6.4 L9 7 L8.8 8 C6.5 8.4 3.6 5.6 4 3.2 Z" fill="#fff"/>
        </svg>
        <span>123-456-7890</span>
      </li>
      <li class="contacts__item">
        <svg class="contacts__icon" viewBox="0 0 12 12" aria-hidden="true">
          <rect x="1" y="2.5" width="10" height="7" fill="#fff"/>
          <path d="M1 2.5 L6 6.5 L11 2.5" fill="none" stroke="var(--teal)" stroke-width="1"/>
        </svg>
        <span>info@brenoloft.com</span>
      </li>
      <li class="contacts__item">
        <svg class="contacts__icon" viewBox="0 0 12 12" aria-hidden="true">
          <circle cx="6" cy="6" r="5.3" fill="none" stroke="#fff" stroke-width="1.2"/>
          <ellipse cx="6" cy="6" rx="2.3" ry="5.3" fill="none" stroke="#fff" stroke-width="1"/>
          <line x1="0.7" y1="6" x2="11.3" y2="6" stroke="#fff" stroke-width="1"/>
        </svg>
        <span>www.brenoloft.com</span>
      </li>
    </ul>
  </section>

  <section class="card card--back" aria-label="Business card back">
    <div class="wordmark">brenoloft</div>
    <div class="follow">
      <span>Follow Us On:</span>
      <span class="follow__badge" aria-hidden="true"></span>
      <span class="follow__badge" aria-hidden="true"></span>
    </div>
    <p class="web-address">www.brenoloft.com</p>
  </section>

</main>
</body>
</html>
```